Sierra Lantern Roots Festival Music Conference & Concert Series needs a banner design to welco...

We are looking for a banner to use as a backdrop where people can take pictures and promote the event as they upload to social media. The music conference primarily targets high school students so we are looking for a design that will attract a younger audience. The festival revolves around music appreciation in the US/Mexico border. We like the "Sierra LanternRoots Festival" trumpet logo on the "5th annual" design attached, but we are open to other designs.
Target Market(s)
ages 15-45
Colors
Designer to choose colors to be used in the design.
Look and feel

```html
<!DOCTYPE html>
<html lang="en">
<head>
<meta charset="utf-8">
<title>Sierra Lantern Roots Festival – Banner</title>
<link rel="stylesheet" href="https://fonts.googleapis.com/css2?family=Open+Sans:wdth,wght@75,700;100,700;100,800&display=swap">
<style>
  :root {
    --magenta: #c20fdc;
    --violet: #7a10d6;
    --indigo: #2a0880;
    --navy: #16055e;
    --pink: #ff19a6;
    --yellow: #ffd80c;
    --white: #ffffff;
  }
  html, body {
    margin: 0;
    padding: 0;
    width: 960px;
    height: 1200px;
    overflow: hidden;
    background: var(--navy);
  }
  .banner {
    position: relative;
    width: 960px;
    height: 1200px;
    overflow: hidden;
    font-family: "Open Sans", Arial, sans-serif;
  }
  .crowd-photo {
    position: absolute;
    inset: 0;
    background:
      radial-gradient(ellipse 60% 35% at 55% 22%, rgba(240, 80, 230, 0.55), transparent 70%),
      linear-gradient(180deg, var(--magenta) 0%, var(--violet) 30%, var(--indigo) 55%, var(--navy) 100%);
  }
  .frame {
    position: absolute;
    inset: 0;
  }
  .annual-pill {
    position: absolute;
    left: 299px;
    top: 484px;
    width: 355px;
    height: 89px;
    border-radius: 30px;
    background: var(--pink);
    color: var(--white);
    font-stretch: 75%;
    font-weight: 700;
    font-size: 50px;
    line-height: 89px;
    text-align: center;
    letter-spacing: 0.5px;
  }
  .title-rules {
    position: absolute;
    left: 0;
    top: 580px;
    width: 960px;
    height: 200px;
  }
  .festival-name {
    position: absolute;
    left: 0;
    width: 960px;
    top: 636px;
    margin: 0;
    text-align: center;
    color: var(--white);
    font-weight: 800;
    font-stretch: 75%;
    font-size: 104px;
    line-height: 110px;
    letter-spacing: 2px;
  }
  .festival-tagline {
    position: absolute;
    left: 0;
    width: 960px;
    top: 786px;
    margin: 0;
    text-align: center;
    font-weight: 700;
    font-stretch: 100%;
    font-size: 84px;
    line-height: 104px;
    letter-spacing: 10px;
  }
  .festival-tagline .word-roots { color: var(--yellow); }
  .festival-tagline .word-festival { color: var(--pink); }
  .event-subtitle {
    position: absolute;
    left: 0;
    width: 960px;
    top: 890px;
    margin: 0;
    text-align: center;
    color: var(--white);
    font-weight: 700;
    font-stretch: 75%;
    font-size: 42px;
    line-height: 50px;
  }
</style>
</head>
<body>
  <main class="banner">
    <div class="crowd-photo" role="img" aria-label="Concert crowd with raised hands under magenta and violet stage lights"></div>

    <svg class="frame" width="960" height="1200" viewBox="0 0 960 1200" aria-hidden="true">
      <rect x="24" y="16" width="915" height="1168" fill="none" stroke="var(--white)" stroke-width="5" stroke-dasharray="12 14"/>
    </svg>

    <div class="annual-pill">5TH ANNUAL</div>

    <svg class="title-rules" width="960" height="200" viewBox="0 0 960 200" aria-hidden="true">
      <line x1="79" y1="38" x2="441" y2="38" stroke="var(--white)" stroke-width="4"/>
      <line x1="502" y1="38" x2="876" y2="38" stroke="var(--white)" stroke-width="4"/>
      <polygon points="474,10 480,26 497,26 484,36 489,52 474,42 459,52 464,36 451,26 468,26"
               fill="none" stroke="var(--white)" stroke-width="3.5" stroke-linejoin="miter"/>
      <line x1="79" y1="185" x2="876" y2="185" stroke="var(--white)" stroke-width="4"/>
    </svg>

    <h1 class="festival-name">SIERRA LANTERN</h1>
    <p class="festival-tagline"><span class="word-roots">ROOTS</span> <span class="word-festival">FESTIVAL</span></p>
    <p class="event-subtitle">MUSIC CONFERENCE &amp; CONCERT SERIES</p>
  </main>
</body>
</html>
```